Brackwell Exteriors Needs a New Website!

We are an exteriors company specializing in vinyl siding, Corwin Maddox siding, aluminum soffit/fascia, trough. We do new construction work as well as renovations. We also build detached garages.
You can view our current website at www.brackwellfabricators.ca
I want to completely overhaul the website.
Our services are different now as we no longer do new home construction as well as we do not do the snow clearing.
I want to focus on 2 things in particular on the website:

1/ Exterior renovations

2/ Detached Garage construction.

I have included our logo in the attached files to use as well.

Some features we would like:

1/ Be able to easily attach a video from Clipverse/Reelio to highlight a product or service
2/ Quick chat or contact button that we can talk to a potential client quickly
3/ Meet the Team page that is interesting and fresh
4/ Place for us to put in helpful exterior tips/suggestions for homeowners.

Content is not important, but looking for the best design that will attract people once they click on our page and want to renovate with us.

Target Market(s)

People looking for renovations on their home, people looking to build a detached garage.

Industry/Entity Type

Residential Construction

Number of Pages Required

5+ page

Font styles to use
Sans Serif

Requirements
Must have
• Fresh and exciting home page.

Simple design. Don't want it over complicated or too much information to confuse the potential client.

Easy way to contact us.

Meet the team page that instills confidence
Nice to have
• Colour of website to go off our logo. Doesn't need to be an exact match, but something that goes well with our blue and grey.

```html
<!DOCTYPE html>
<html lang="en">
<head>
<meta charset="utf-8">
<title>Brackwell Builders</title>
<link href="https://fonts.googleapis.com/css2?family=Montserrat:wght@300;400;500;600;700;800&display=swap" rel="stylesheet">
<style>
:root{
  --blue:#1b58a8;
  --blue-dark:#144a8f;
  --ink:#232323;
  --grey:#6a6a6a;
  --grey-btn:#626262;
  --grey-bar:#7b7b7b;
  --light:#f1f1f1;
  --footer:#151515;
  --white:#ffffff;
}
*{margin:0;padding:0;box-sizing:border-box}
html,body{width:1200px;height:4280px;overflow:hidden}
body{font-family:'Montserrat',sans-serif;color:var(--ink);background:var(--white);position:relative}
.abs{position:absolute}
.topbar{left:0;top:0;width:1200px;height:42px}
.topbar-social{left:150px;top:12px;display:flex;gap:12px}
.topbar-social span{width:16px;height:16px;border-radius:50%;background:var(--white);opacity:.9}
.topbar-call{left:608px;top:10px;color:var(--white);font-size:19px;font-weight:500;display:flex;align-items:center;gap:8px}
.topbar-call b{font-weight:700}
.topbar-quote{left:906px;top:11px;color:var(--white);font-size:15px;font-weight:700;letter-spacing:.3px}
.brand{left:145px;top:50px;display:flex;align-items:center;gap:12px}
.brand-dot{width:72px;height:72px;border-radius:50%;border:6px solid var(--blue)}
.brand-name{font-size:25px;font-weight:700;color:var(--blue);line-height:1.05;letter-spacing:.5px}
.nav{top:73px;left:0;width:1200px;height:20px;font-size:14px;font-weight:600;color:#333}
.nav a{position:absolute;text-decoration:none;color:inherit;letter-spacing:.3px}
.nav-marker{left:489px;top:122px;width:56px;height:6px;background:var(--blue)}
.hero-title{left:0;top:268px;width:1200px;text-align:center;color:var(--white);font-size:79px;font-weight:800;letter-spacing:2px;text-shadow:0 3px 8px rgba(0,0,0,.35)}
.hero-sub{left:0;top:390px;width:1200px;text-align:center;color:var(--white);font-size:21px;font-weight:500;line-height:30px;text-shadow:0 2px 6px rgba(0,0,0,.5)}
.btn{position:absolute;display:flex;align-items:center;justify-content:center;gap:10px;border-radius:30px;font-weight:600;color:var(--white);text-decoration:none}
.btn-blue{background:var(--blue);font-size:16px}
.btn-grey{background:var(--grey-btn);font-size:16px}
.btn-ghost{border:3px solid var(--white);font-size:16px;background:rgba(0,0,0,.35)}
.arrow-dot{width:13px;height:13px;border-radius:50%;background:var(--white);position:relative}
.arrow-dot::after{content:"";position:absolute;left:4px;top:3px;border-left:5px solid var(--blue);border-top:3.5px solid transparent;border-bottom:3.5px solid transparent}
.btn-grey .arrow-dot::after{border-left-color:var(--grey-btn)}
.btn-ghost .arrow-dot::after{border-left-color:#333}
.dots{left:554px;top:605px;display:flex;gap:8px}
.dots span{width:12px;height:12px;border-radius:50%;background:var(--white)}
.dots span.on{background:var(--blue)}
.h-section{font-size:42px;font-weight:800;letter-spacing:1px;color:var(--ink)}
.h-section em{font-style:normal;font-weight:300;color:var(--blue)}
.rule{height:4px;width:62px;background:#4a4a4a}
.about-title{left:600px;top:826px;font-size:40px;font-weight:800}
.about-name{left:600px;top:878px;display:flex;align-items:center;gap:12px;font-size:41px;font-weight:300;color:var(--blue)}
.about-name::before{content:"";width:60px;height:4px;background:#4a4a4a}
.body-copy{font-size:14px;line-height:31.5px;color:#555}
.service-title{color:var(--white);font-size:40px;font-weight:800;line-height:43px;letter-spacing:.5px;text-shadow:0 3px 6px rgba(0,0,0,.5)}
.work{position:absolute}
.contact-item{top:3400px;display:flex;align-items:center;gap:14px;font-size:18px;font-weight:500;color:#333}
.ci-icon{width:42px;height:42px;border-radius:50%;display:flex;align-items:center;justify-content:center}
.field{position:absolute;background:var(--white);border:1px solid #c9c9c9;font-size:14px;color:#444;padding:16px 22px}
.footer-social{top:4078px;left:497px;display:flex;gap:10px}
.footer-social span{width:44px;height:44px;border-radius:50%;border:2px solid var(--white);display:flex;align-items:center;justify-content:center}
.footer-social span::after{content:"";width:8px;height:8px;border-radius:50%;background:var(--white)}
.footer-nav{top:4158px;left:0;width:1200px;display:flex;justify-content:center;gap:36px;color:var(--white);font-size:19px;font-weight:600}
.footer-copy{top:4208px;left:0;width:1200px;text-align:center;color:#cfcfcf;font-size:12px}
</style>
</head>
<body>

<!-- Top bar -->
<svg class="abs topbar" width="1200" height="42" viewBox="0 0 1200 42">
  <rect width="1200" height="42" fill="var(--grey-bar)"/>
  <polygon points="0,0 882,0 860,42 0,42" fill="var(--blue)"/>
</svg>
<div class="abs topbar-social"><span></span><span></span><span></span><span></span></div>
<div class="abs topbar-call">
  <svg width="16" height="16" viewBox="0 0 24 24"><path fill="#fff" d="M6.6 10.8a15 15 0 0 0 6.6 6.6l2.2-2.2c.3-.3.7-.4 1-.2 1.1.4 2.3.6 3.6.6.6 0 1 .4 1 1V20c0 .6-.4 1-1 1A17 17 0 0 1 3 4c0-.6.4-1 1-1h3.5c.6 0 1 .4 1 1 0 1.3.2 2.5.6 3.6.1.3 0 .7-.2 1z"/></svg>
  Call us : <b>555-014-2290</b>
</div>
<div class="abs topbar-quote">REQUEST A QUOTE</div>

<!-- Header -->
<header>
  <div class="abs brand"><span class="brand-dot"></span><span class="brand-name">BRACKWELL<br>EXTERIORS</span></div>
  <nav class="abs nav">
    <a style="left:494px">HOME</a>
    <a style="left:568px">ABOUT US</a>
    <a style="left:675px">SERVICES</a>
    <a style="left:776px">TEAM</a>
    <a style="left:847px">SUGGESTIONS</a>
    <a style="left:982px">CONTACT</a>
  </nav>
  <div class="abs nav-marker"></div>
</header>

<!-- Hero -->
<svg class="abs" style="left:0;top:128px" width="1200" height="670" viewBox="0 0 1200 670">
  <defs>
    <linearGradient id="heroGrad" x1="0" y1="0" x2="0" y2="1">
      <stop offset="0" stop-color="#4f86c9"/>
      <stop offset=".35" stop-color="#8fa9c4"/>
      <stop offset=".6" stop-color="#6e6a6c"/>
      <stop offset=".85" stop-color="#4d4a44"/>
      <stop offset="1" stop-color="#5b6b3c"/>
    </linearGradient>
  </defs>
  <rect width="1200" height="670" fill="url(#heroGrad)" role="img" aria-label="Two-storey house with covered front porch under a sunny blue sky"/>
  <path d="M0,640 Q300,600 600,572 Q900,600 1200,640 L1200,670 L0,670 Z" fill="var(--white)"/>
  <path d="M0,636 Q300,596 600,568 Q900,596 1200,636" fill="none" stroke="var(--blue)" stroke-width="7"/>
</svg>
<h1 class="abs hero-title">BRACKWELL BUILDERS</h1>
<p class="abs hero-sub">Honest and reliable construction service in Edmonton and area.<br>We take pride in each and every project</p>
<a class="btn btn-blue" style="left:484px;top:484px;width:234px;height:57px">REQUEST A QUOTE <span class="arrow-dot"></span></a>
<div class="abs dots"><span></span><span></span><span class="on"></span><span></span><span></span></div>

<!-- About -->
<svg class="abs" style="left:140px;top:810px" width="412" height="412" viewBox="0 0 412 412">
  <defs>
    <linearGradient id="aboutGrad" x1="0" y1="0" x2="0" y2="1">
      <stop offset="0" stop-color="#b9c6d6"/>
      <stop offset=".4" stop-color="#8c7a6a"/>
      <stop offset=".75" stop-color="#6b6a55"/>
      <stop offset="1" stop-color="#4f8a2e"/>
    </linearGradient>
  </defs>
  <circle cx="206" cy="206" r="203" fill="url(#aboutGrad)" role="img" aria-label="Stone and stucco house exterior with iron fence and lawn"/>
</svg>
<h2 class="abs h-section about-title">ABOUT</h2>
<div class="abs about-name">BRACKWELLBUILDERS</div>
<p class="abs body-copy" style="left:600px;top:940px;width:450px">Sed ut perspiciatis unde omnis iste natus error sit voluptatem accusantium doloremque laudantium, totam rem aperiam, eaque ipsa quae ab illo inventore veritatis et quasi architecto beatae vitae dicta sunt explicabo. Nemo enim ipsam voluptatem quia voluptas sit aspernatur aut odit aut fugit, sed quia consequuntur magni dolores eos qui ratione</p>
<a class="btn btn-grey" style="left:600px;top:1152px;width:181px;height:45px">READ MORE <span class="arrow-dot"></span></a>

<!-- Services -->
<svg class="abs" style="left:0;top:1258px" width="1200" height="592" viewBox="0 0 1200 592">
  <defs>
    <linearGradient id="renoGrad" x1="0" y1="0" x2="0" y2="1">
      <stop offset="0" stop-color="#2f4fb8"/>
      <stop offset=".45" stop-color="#3a4f7a"/>
      <stop offset=".75" stop-color="#3a3a36"/>
      <stop offset="1" stop-color="#6a5a3a"/>
    </linearGradient>
    <linearGradient id="garageGrad" x1="0" y1="0" x2="0" y2="1">
      <stop offset="0" stop-color="#b9c6d4"/>
      <stop offset=".4" stop-color="#a08a6c"/>
      <stop offset=".75" stop-color="#8b6a45"/>
      <stop offset="1" stop-color="#7a6a55"/>
    </linearGradient>
  </defs>
  <rect x="0" y="0" width="595" height="592" fill="url(#renoGrad)" role="img" aria-label="Modern home exterior at dusk with metal roof and lit garage doors"/>
  <rect x="600" y="0" width="600" height="592" fill="url(#garageGrad)" role="img" aria-label="Detached garage under construction with roof trusses and sheathing"/>
  <polygon points="0,0 1200,0 1200,8 600,83 0,8" fill="var(--white)"/>
  <polyline points="0,8 600,83 1200,8" fill="none" stroke="var(--blue)" stroke-width="6"/>
  <polygon points="0,592 0,585 600,505 1200,585 1200,592" fill="var(--white)"/>
  <polyline points="0,585 600,505 1200,585" fill="none" stroke="var(--blue)" stroke-width="6"/>
  <rect x="595" y="0" width="5" height="592" fill="var(--white)"/>
</svg>
<h3 class="abs service-title" style="left:146px;top:1507px">EXTERIOR<br>RENOVATIONS</h3>
<a class="btn btn-ghost" style="left:145px;top:1629px;width:172px;height:50px">READ MORE <span class="arrow-dot"></span></a>
<h3 class="abs service-title" style="left:669px;top:1507px">DETACHED GARAGE<br>CONSTRUCTION</h3>
<a class="btn btn-ghost" style="left:668px;top:1629px;width:172px;height:50px">READ MORE <span class="arrow-dot"></span></a>

<!-- Featured works -->
<h2 class="abs h-section" style="left:0;top:1889px;width:1200px;text-align:center">FEATURED <em>WORKS</em></h2>
<div class="abs rule" style="left:569px;top:1953px"></div>
<svg class="abs" style="left:145px;top:2019px" width="911" height="490" viewBox="0 0 911 490">
  <defs>
    <linearGradient id="w1" x1="0" y1="0" x2="0" y2="1"><stop offset="0" stop-color="#e8e6e2"/><stop offset=".5" stop-color="#8b6c55"/><stop offset="1" stop-color="#b69a7a"/></linearGradient>
    <linearGradient id="w2" x1="0" y1="0" x2="0" y2="1"><stop offset="0" stop-color="#2f6cc0"/><stop offset=".35" stop-color="#3b3f48"/><stop offset=".7" stop-color="#5a4a30"/><stop offset="1" stop-color="#a8a69e"/></linearGradient>
    <linearGradient id="w3" x1="0" y1="0" x2="0" y2="1"><stop offset="0" stop-color="#d8d9d7"/><stop offset=".5" stop-color="#8a6a4e"/><stop offset="1" stop-color="#6c7a4a"/></linearGradient>
    <linearGradient id="w4" x1="0" y1="0" x2="1" y2="0"><stop offset="0" stop-color="#a8876a"/><stop offset=".5" stop-color="#9c9c9a"/><stop offset="1" stop-color="#d4d4d2"/></linearGradient>
    <linearGradient id="w5" x1="0" y1="0" x2="0" y2="1"><stop offset="0" stop-color="#3b5a8a"/><stop offset=".5" stop-color="#7a6e5a"/><stop offset="1" stop-color="#a3a19c"/></linearGradient>
  </defs>
  <rect x="0" y="0" width="296" height="238" fill="url(#w1)" role="img" aria-label="Brick two-storey home under construction"/>
  <rect x="307" y="0" width="297" height="490" fill="url(#w2)" role="img" aria-label="Dark wood-clad house with steep gable roof"/>
  <rect x="615" y="0" width="296" height="238" fill="url(#w3)" role="img" aria-label="Hand holding a magnifying glass over a home facade"/>
  <rect x="0" y="251" width="296" height="239" fill="url(#w4)" role="img" aria-label="Cross-section of wall insulation layers and brick"/>
  <rect x="615" y="251" width="296" height="239" fill="url(#w5)" role="img" aria-label="Modern garage with lit doors and concrete driveway"/>
  <circle cx="455" cy="243" r="16" fill="none" stroke="#fff" stroke-width="3.5"/>
  <line x1="467" y1="255" x2="478" y2="266" stroke="#fff" stroke-width="4" stroke-linecap="round"/>
  <line x1="447" y1="243" x2="463" y2="243" stroke="#fff" stroke-width="3"/>
  <line x1="455" y1="235" x2="455" y2="251" stroke="#fff" stroke-width="3"/>
</svg>

<!-- Exterior tips -->
<svg class="abs" style="left:0;top:2623px" width="1200" height="548" viewBox="0 0 1200 548">
  <defs>
    <linearGradient id="tipsGrad" x1="0" y1="0" x2="0" y2="1">
      <stop offset="0" stop-color="#26344f"/>
      <stop offset=".45" stop-color="#6a6d78"/>
      <stop offset=".75" stop-color="#b6a389"/>
      <stop offset="1" stop-color="#2f7fb8"/>
    </linearGradient>
  </defs>
  <rect width="1200" height="548" fill="var(--light)"/>
  <polygon points="656,0 1200,0 1200,548 645,548 598,274" fill="url(#tipsGrad)" role="img" aria-label="Modern white house at dusk with glass walls and a pool"/>
  <circle cx="602" cy="274" r="46" fill="var(--white)" stroke="#d8d8d8" stroke-width="3"/>
  <circle cx="892" cy="274" r="38" fill="none" stroke="#fff" stroke-width="5"/>
  <polygon points="882,254 882,294 911,274" fill="#fff"/>
</svg>
<h2 class="abs h-section" style="left:143px;top:2710px">EXTERIOR <em>TIPS</em></h2>
<div class="abs rule" style="left:143px;top:2770px"></div>
<p class="abs body-copy" style="left:143px;top:2814px;width:385px">Sed ut perspiciatis unde omnis iste natus error sit voluptatem accusantium doloremque laudantium, totam rem aperiam, eaque ipsa quae ab illo inventore veritatis et quasi architecto beatae vitae dicta sunt explicabo. Nemo enim ipsam voluptatem quia voluptas sit aspernatur aut odit</p>
<a class="btn btn-grey" style="left:143px;top:3028px;width:182px;height:46px">READ MORE <span class="arrow-dot"></span></a>

<!-- Contact -->
<svg class="abs" style="left:0;top:3171px" width="1200" height="830" viewBox="0 0 1200 830">
  <defs>
    <linearGradient id="contactGrad" x1="0" y1="0" x2="0" y2="1">
      <stop offset="0" stop-color="#f6f6f5"/>
      <stop offset=".5" stop-color="#ecebe8"/>
      <stop offset="1" stop-color="#dfe3da"/>
    </linearGradient>
  </defs>
  <rect width="1200" height="830" fill="url(#contactGrad)" role="img" aria-label="Faded photo of a suburban home with front lawn"/>
  <path d="M0,751 Q300,780 598,821 Q900,780 1200,751 L1200,830 L0,830 Z" fill="var(--footer)"/>
  <path d="M0,747 Q300,776 598,817 Q900,776 1200,747" fill="none" stroke="var(--blue)" stroke-width="7"/>
</svg>
<h2 class="abs h-section" style="left:0;top:3277px;width:1200px;text-align:center">CONTACT <em>FORM</em></h2>
<div class="abs rule" style="left:569px;top:3340px"></div>
<div class="abs contact-item" style="left:292px">
  <span class="ci-icon" style="background:var(--blue)"><svg width="20" height="20" viewBox="0 0 24 24"><path fill="#fff" d="M6.6 10.8a15 15 0 0 0 6.6 6.6l2.2-2.2c.3-.3.7-.4 1-.2 1.1.4 2.3.6 3.6.6.6 0 1 .4 1 1V20c0 .6-.4 1-1 1A17 17 0 0 1 3 4c0-.6.4-1 1-1h3.5c.6 0 1 .4 1 1 0 1.3.2 2.5.6 3.6.1.3 0 .7-.2 1z"/></svg></span>
  Phone : 555-014-2290
</div>
<div class="abs contact-item" style="left:580px">
  <span class="ci-icon" style="background:var(--grey-btn)"><svg width="20" height="16" viewBox="0 0 20 16"><rect x="1" y="1" width="18" height="14" rx="1.5" fill="#fff"/><polyline points="1.5,2 10,9 18.5,2" fill="none" stroke="#626262" stroke-width="1.8"/></svg></span>
  Email: info@brackwellexteriors.ca
</div>
<div class="field" style="left:204px;top:3490px;width:385px;height:50px">First Name *</div>
<div class="field" style="left:612px;top:3490px;width:384px;height:50px">Last Name *</div>
<div class="field" style="left:204px;top:3565px;width:385px;height:50px">Email *</div>
<div class="field" style="left:612px;top:3565px;width:384px;height:50px">Phone</div>
<div class="field" style="left:204px;top:3640px;width:792px;height:116px">Message</div>
<a class="btn btn-blue" style="left:483px;top:3793px;width:234px;height:58px">REQUEST A QUOTE <span class="arrow-dot"></span></a>

<!-- Footer -->
<div class="abs" style="left:0;top:4001px;width:1200px;height:279px;background:var(--footer)"></div>
<svg class="abs" style="left:572px;top:3965px" width="52" height="52" viewBox="0 0 52 52">
  <circle cx="26" cy="26" r="24" fill="var(--white)"/>
  <line x1="26" y1="38" x2="26" y2="14" stroke="var(--blue)" stroke-width="2.5"/>
  <polyline points="19,21 26,14 33,21" fill="none" stroke="var(--blue)" stroke-width="2.5"/>
</svg>
<div class="abs footer-social"><span></span><span></span><span></span><span></span></div>
<nav class="abs footer-nav"><span>HOME</span><span>ABOUT US</span><span>SERVICES</span><span>TEAM</span><span>SUGGESTIONS</span><span>CONTACT</span></nav>
<p class="abs footer-copy">© 2020 Brackwell Builders . All right reserved &nbsp;Term of Use &nbsp;|&nbsp; Privacy policy</p>

</body>
</html>
```